Steadfast Field Crews

We are a underground coal mining labour hire company, needing a website that links into our online payroll (www.wagelinkr.com.au) and also need to have job applications page that is a preform with drop down menu,s with answers or check boxes. We would also need a 3 tier administration access for access to different files.
We are looking for an ongoing relationship with future app integration

Reason: There are a few more designs to come and I'm out at the mine for another week

Industry/Entity Type

Coal Mining

```html
<!DOCTYPE html>
<html lang="en">
<head>
<meta charset="utf-8">
<title>FIELDCOAL – Steadfast Field Crews</title>
<link href="https://fonts.googleapis.com/css2?family=Lato:ital,wght@0,300;0,400;0,700;1,400&display=swap" rel="stylesheet">
<style>
:root{
  --orange:#ef7a2a;
  --orange-light:#f59a4e;
  --orange-dark:#e2661b;
  --black:#0b0b0b;
  --ink:#1c1c1c;
  --header-text:#cfcfcf;
  --brand-text:#9a9a9a;
  --border:#cfcfcf;
  --footer:#222;
}
*{margin:0;padding:0;box-sizing:border-box}
html,body{width:874px;height:1200px;overflow:hidden;background:#fff}
body{font-family:"Lato",sans-serif;color:var(--ink);position:relative}
.abs{position:absolute}

/* header */
.site-header{left:0;top:0;width:874px;height:178px;background:linear-gradient(#5b5b5b 0,#1a1a1a 28px,var(--black) 40px)}
.crew-mark{left:50px;top:78px;display:flex;align-items:center;gap:7px;color:var(--orange);font-size:13px;font-weight:700;line-height:1.15;width:120px}
.crew-mark .dot{width:14px;height:14px;border-radius:50%;background:var(--orange);flex:none}
.payroll-brand{left:350px;top:112px;font-size:30px;font-weight:300;color:var(--brand-text);line-height:1}
.contact{left:586px;top:44px;color:var(--header-text);font-size:11.5px;line-height:19.2px}
.contact .row{position:relative;padding-left:17px}
.contact svg{position:absolute;left:0;top:3px}
.social{left:600px;top:130px;display:flex;gap:14px}
.social i{width:15px;height:15px;border-radius:50%;background:#b5b5b5;display:block}

/* nav */
.main-nav{left:0;top:178px;width:874px;height:44px;background:linear-gradient(var(--orange-light),var(--orange))}
.main-nav a{position:absolute;top:0;height:44px;line-height:42px;font-size:10.5px;color:#1a1a1a;text-decoration:none}
.main-nav a.active{background:var(--orange-dark);color:#fff;padding:0 24px;left:53px}
.shadow{left:53px;width:766px;height:18px;background:radial-gradient(ellipse at 50% 0,rgba(0,0,0,.28),rgba(0,0,0,0) 70%)}

/* hero */
.hero{left:53px;top:251px;width:766px;height:295px;overflow:hidden}
.hero-photo{position:absolute;inset:0;background:linear-gradient(170deg,#cfd5da 0,#9f8a78 16%,#6e5240 45%,#3f3027 75%,#584436 100%)}
.hero svg.curve{position:absolute;left:0;top:0}
.hero h1{position:absolute;left:13px;top:124px;font-weight:300;font-size:24.5px;color:#fff;letter-spacing:.2px}
.hero p{position:absolute;left:15px;top:163px;font-style:italic;font-size:11px;line-height:24px;color:#3a1d08;width:230px}
.hero .arrow{position:absolute;top:250px;width:26px;height:26px;border-radius:50%;background:rgba(150,150,150,.7);border:2px solid rgba(220,220,220,.6)}

/* about */
.about-title{left:53px;top:584px;width:184px;height:40px;background:var(--orange);color:#fff;font-size:17.5px;font-weight:300;padding:9px 11px}
.about-title b{font-weight:400}
.about-text{left:53px;top:633px;width:182px;font-size:11.3px;line-height:24px;text-align:justify;color:#111}

/* cards */
.card{top:584px;width:176px;height:254px;border:1px solid var(--border)}
.card h2{position:absolute;left:13px;top:9px;font-size:14px;font-weight:700;color:var(--orange)}
.card .photo{position:absolute;left:15px;top:45px;width:144px;height:80px}
.card ul{position:absolute;left:14px;list-style:none;font-size:10.4px;line-height:14px;color:#555;width:155px}
.card li{position:relative;padding-left:19px;margin-bottom:10px}
.card li::before{content:"→";position:absolute;left:0;top:-1px;color:#111}
.card .more{position:absolute;left:15px;font-size:10.5px;color:var(--orange)}

/* commitment */
.commit{left:53px;top:880px;width:766px;height:40px;background:var(--orange);color:#fff;font-size:14.5px;font-weight:300;padding:11px 10px}
.feature .photo{width:220px;height:102px}
.feature p{font-size:9.8px;line-height:24px;margin-top:4px;color:#222}
.rule{left:53px;top:1119px;width:768px;height:1px;background:#ccc}

/* footer */
.site-footer{left:0;top:1146px;width:874px;height:54px;background:var(--footer);text-align:center}
.site-footer nav a{position:absolute;top:12px;font-size:10.5px;color:#ddd;text-decoration:none}
.site-footer small{position:absolute;left:0;width:874px;top:33px;font-size:9.6px;color:#aaa}
</style>
</head>
<body>

<header class="abs site-header">
  <div class="abs crew-mark"><span class="dot"></span>Steadfast Field Crews</div>
  <div class="abs payroll-brand">wagelinkr</div>
  <div class="abs contact">
    <div class="row"><svg width="9" height="12" viewBox="0 0 9 12"><path d="M4.5 0A4.5 4.5 0 0 0 0 4.5C0 8 4.5 12 4.5 12S9 8 9 4.5A4.5 4.5 0 0 0 4.5 0Zm0 6.3a1.8 1.8 0 1 1 0-3.6 1.8 1.8 0 0 1 0 3.6Z" fill="#ef7a2a"/></svg>FIELDCOAL</div>
    <div class="row">Coal Mine Services</div>
    <div class="row">Address: 18 Banksia Rd, Ridgefield NSW 2291</div>
    <div class="row"><svg width="10" height="11" viewBox="0 0 10 11"><path d="M2 0 4 2.5 3 4c.6 1.6 2 3 3.6 3.7l1.4-1 2 2L8.6 11C4 10.5.4 6.8 0 2.2Z" fill="#ef7a2a"/></svg>1800-555-0142</div>
  </div>
  <div class="abs social"><i></i><i></i><i></i><i></i></div>
</header>

<nav class="abs main-nav">
  <a class="active" href="#">Home</a>
  <a href="#" style="left:144px">Apply for position</a>
  <a href="#" style="left:265px">Pay Portal</a>
  <a href="#" style="left:350px">Download</a>
  <a href="#" style="left:436px">Mission</a>
  <a href="#" style="left:510px">About us</a>
  <a href="#" style="left:590px">Contact us</a>
</nav>
<div class="abs shadow" style="top:222px"></div>

<section class="abs hero">
  <div class="hero-photo" role="img" aria-label="Aerial view of a terraced open cut coal mine"></div>
  <svg class="curve" width="766" height="295" viewBox="0 0 766 295"><path d="M0 0H211Q344 150 215 295H0Z" fill="#ef7a2a"/></svg>
  <h1>FIELDCOAL Underground</h1>
  <p>We are a labor hire company for major mining services company</p>
  <span class="arrow" style="left:693px"></span>
  <span class="arrow" style="left:724px"></span>
</section>
<div class="abs shadow" style="top:546px"></div>

<div class="abs about-title">About <b>fieldcoal</b></div>
<p class="abs about-text">We are KRMT pty ltd trading as Steadfast Field Crews, we are experienced in ground consolidation in underground coal mines, in short when they collapse or cave in we come in with chemical pumps and stabilise the ground or fill cavities which will then allow for the mining process to continue...</p>

<article class="abs card" style="left:253px">
  <h2>Underground</h2>
  <div class="photo" role="img" aria-label="Dim underground mine tunnel" style="background:linear-gradient(110deg,#3a2a12,#7a5a22 45%,#2a1d0c)"></div>
  <ul style="top:152px">
    <li>Underground roadway development</li>
    <li>Installation of conveyors</li>
    <li>Longwall relocation and maintenance</li>
  </ul>
</article>

<article class="abs card" style="left:446px">
  <h2>Services</h2>
  <div class="photo" role="img" aria-label="Mine workers in hard hats beside drilling equipment" style="background:linear-gradient(100deg,#3c3c3c,#8a8a8a 45%,#2b2f5a 65%,#4a4a4a)"></div>
  <ul style="top:142px">
    <li>Open cut electrical services</li>
    <li>Open cut mechanical</li>
    <li>Maintenance and relief services</li>
  </ul>
  <span class="more" style="top:229px">Learn More</span>
</article>

<article class="abs card" style="left:645px">
  <h2>Engineering</h2>
  <div class="photo" role="img" aria-label="Engineering crew seated beside heavy machinery" style="background:linear-gradient(100deg,#2f2a25,#6a625a 50%,#9a9590)"></div>
  <ul style="top:142px">
    <li>Open cut electrical services</li>
    <li>Open cut mechanical</li>
    <li>services to production plants</li>
  </ul>
  <span class="more" style="top:230px">Learn More</span>
</article>

<div class="abs commit">Our commitment to Clients is a quality service at a fair price.</div>

<div class="abs feature" style="left:53px;top:948px">
  <div class="photo" role="img" aria-label="Coal mine surface plant on a wooded hillside" style="background:linear-gradient(#c5d3e0 0,#4a5a3a 35%,#3f4a36 70%,#6a7080)"></div>
  <p>Lorem ipsum dolor sit amet, consectetur<br>adipisicing elit, sed do eiusmod tempor incididunt</p>
</div>
<div class="abs feature" style="left:325px;top:948px">
  <div class="photo" role="img" aria-label="Mine cart on rails in a lit tunnel" style="background:radial-gradient(circle at 30% 40%,#e0b27a,#8a5a30 50%,#3a2614)"></div>
  <p>Lorem ipsum dolor sit amet, consectetur<br>adipisicing elit, sed do eiusmod tempor incididunt</p>
</div>
<div class="abs feature" style="left:599px;top:948px">
  <div class="photo" role="img" aria-label="Yellow bucket wheel excavator close-up" style="background:linear-gradient(120deg,#7a5a2a,#d4a02a 50%,#a87a1a)"></div>
  <p>Lorem ipsum dolor sit amet, consectetur<br>adipisicing elit, sed do eiusmod tempor incididunt</p>
</div>

<div class="abs rule"></div>

<footer class="abs site-footer">
  <nav>
    <a href="#" style="left:155px">Home</a>
    <a href="#" style="left:222px">Apply for position</a>
    <a href="#" style="left:343px">Pay Portal</a>
    <a href="#" style="left:428px">Download</a>
    <a href="#" style="left:515px">Mission</a>
    <a href="#" style="left:588px">About us</a>
    <a href="#" style="left:668px">Contact us</a>
  </nav>
  <small>Copyright © 2014 All Rights Reserved</small>
</footer>

</body>
</html>
```